Corvane Capital Business Cards

These are professional business cards that are for my family office.
Put fake emails and phone numbers as of now until I finalize those components. This family office controls my families investments, assets, and future. The cards should be professional.
..
.
.
.
I just uploaded another variation of a logo I would like to see as a business card to I am inbeteen which logo to use

Target Market(s)

business

Industry/Entity Type

business

Contact Information for Business Card

Professional, wealth related, finance related.

Requirements
Must have
• Logo

```html
<!DOCTYPE html>
<html lang="en">
<head>
<meta charset="utf-8">
<title>Corvane Capital Business Cards</title>
<link rel="stylesheet" href="https://fonts.googleapis.com/css2?family=Cinzel:wght@400;700&family=Arimo:wght@400&display=swap">
<style>
  :root {
    --backdrop: #3d3d3d;
    --paper: #ffffff;
    --navy: #1b2030;
    --ink: #1b2030;
    --muted: #8a8a8a;
    --body: #4a4a4a;
    --light: #ffffff;
  }
  * { box-sizing: border-box; margin: 0; padding: 0; }
  html, body {
    width: 1200px; height: 803px; overflow: hidden;
    background: var(--backdrop);
  }
  .sheet {
    position: relative; width: 1200px; height: 803px;
    display: flex; align-items: center; justify-content: center; gap: 40px;
  }
  .card {
    position: relative; width: 540px; height: 310px;
    border-radius: 22px; overflow: hidden;
  }
  .card--front { background: var(--paper); }
  .card--back {
    background: var(--navy);
    display: flex; flex-direction: column; align-items: center; justify-content: center;
  }

  /* front */
  .front__brand {
    position: absolute; left: 38px; top: 40px;
    font-family: "Cinzel", serif; font-weight: 400;
    font-size: 25px; letter-spacing: 1px; color: var(--ink);
  }
  .front__person { position: absolute; left: 38px; top: 98px; }
  .person__name {
    font-family: "Cinzel", serif; font-weight: 700;
    font-size: 22px; color: var(--ink); line-height: 1;
  }
  .person__role {
    font-family: "Arimo", sans-serif; font-size: 12px;
    color: var(--muted); margin-top: 3px;
  }
  .front__address {
    position: absolute; left: 38px; top: 150px;
    font-family: "Arimo", sans-serif; font-size: 13px;
    color: var(--body); line-height: 1.35;
  }
  .front__contacts {
    position: absolute; left: 38px; top: 196px; list-style: none;
    font-family: "Arimo", sans-serif; font-size: 13px; color: var(--body);
  }
  .contact { display: flex; align-items: center; gap: 8px; line-height: 1.55; }
  .contact svg { width: 11px; height: 11px; flex: none; }
  .front__mark {
    position: absolute; right: 34px; top: 44px;
    width: 222px; height: 222px;
  }

  /* back */
  .back__mark { width: 130px; height: 130px; }
  .back__brand {
    margin-top: 26px;
    font-family: "Cinzel", serif; font-weight: 400;
    font-size: 28px; letter-spacing: 1px; color: var(--light);
  }
</style>
</head>
<body>
<main class="sheet">
  <section class="card card--front" aria-label="Card front">
    <h1 class="front__brand">Corvane Capital</h1>
    <div class="front__person">
      <p class="person__name">Daniel Reyes</p>
      <p class="person__role">President</p>
    </div>
    <address class="front__address">
      412 Harbor Crest Road<br>
      Kelmont, Canada 48210
    </address>
    <ul class="front__contacts">
      <li class="contact">
        <svg viewBox="0 0 12 12" aria-hidden="true"><path d="M3 1 L5 3.5 L3.8 5 C4.5 6.5 5.5 7.5 7 8.2 L8.5 7 L11 9 L9.5 11 C5 10.5 1.5 7 1 2.5 Z" fill="var(--ink)"/></svg>
        555-210-4418
      </li>
      <li class="contact">
        <svg viewBox="0 0 12 12" aria-hidden="true"><rect x="2.5" y="0.8" width="7" height="10.4" rx="1" fill="none" stroke="var(--ink)" stroke-width="1.3"/></svg>
        555-210-4472
      </li>
      <li class="contact">
        <svg viewBox="0 0 12 12" aria-hidden="true"><rect x="1" y="2" width="10" height="8" fill="var(--ink)"/><path d="M1.5 2.5 L6 6.5 L10.5 2.5" fill="none" stroke="var(--paper)" stroke-width="1"/></svg>
        info@corvanecapital.com
      </li>
      <li class="contact">
        <svg viewBox="0 0 12 12" aria-hidden="true"><circle cx="6" cy="6" r="5" fill="var(--ink)"/><path d="M1 6 H11 M6 1 C3.5 4 3.5 8 6 11 M6 1 C8.5 4 8.5 8 6 11" fill="none" stroke="var(--paper)" stroke-width="0.8"/></svg>
        www.corvanecapital.com
      </li>
    </ul>
    <svg class="front__mark" viewBox="0 0 222 222" aria-hidden="true">
      <circle cx="111" cy="111" r="107" fill="none" stroke="var(--ink)" stroke-width="5"/>
    </svg>
  </section>

  <section class="card card--back" aria-label="Card back">
    <svg class="back__mark" viewBox="0 0 130 130" aria-hidden="true">
      <circle cx="65" cy="65" r="62" fill="none" stroke="var(--light)" stroke-width="3"/>
    </svg>
    <p class="back__brand">Corvane Capital</p>
  </section>
</main>
</body>
</html>
```